Business card design needed

My business is in Matchmaking. My objective is to find the most compatible partner for my clients....basically I'm in the love and happiness industry bringing two people together for a lasting loving relationship.

I envision the design to be something with 2 people who are in love looking happy or even a silhouette.....I don't really know, I'm open to ideas.....maybe no picture at all, but I want it to be classy :-)

I do have a logo which I will upload. You can also go to my website to give you an idea on the colours and the design if that helps, however the website is not finished yet, it should be up by today or tomorrow. If the website has a heart with swirls on the upper left hand corner, that is the old website, please ignore that one. The one that will be up shortly has a picture frame on the home page with my logo that will be in the file I will upload on this page.

Target Market(s)

There are three categories: Over 45, Asian and Western and same sex, but would be able to afford to hire a matchmaker

Contact Information for Business Card

The Tidewell Bureau
Helping You Find The "One"
Mavis Ellery
Matchmaker
0492 517 264
info@tidewellbureau.com.au
www.tidewellbureau.com.au

```html
<!DOCTYPE html>
<html lang="en">
<head>
<meta charset="utf-8">
<title>The Tidewell Bureau – Business Card</title>
<link rel="stylesheet" href="https://fonts.googleapis.com/css2?family=Open+Sans:wdth,wght@75..100,600..800&display=swap">
<style>
  :root {
    --mauve: #8a6670;
    --mauve-deep: #6f4f59;
    --white: #ffffff;
    --photo-dark: #2b2b2b;
    --photo-mid: #8c8c8c;
    --photo-light: #d9d9d9;
    --divider: #e4e4e4;
  }
  * { margin: 0; padding: 0; box-sizing: border-box; }
  html, body {
    width: 1200px;
    height: 693px;
    overflow: hidden;
    background: var(--white);
  }
  .card {
    position: relative;
    width: 1200px;
    height: 693px;
    background: var(--white);
    font-family: "Open Sans", Arial, sans-serif;
    font-stretch: 80%;
  }
  .card__photo {
    position: absolute;
    left: 0;
    top: 0;
    width: 468px;
    height: 693px;
    background:
      radial-gradient(ellipse at 55% 45%, var(--photo-light) 0%, var(--photo-mid) 45%, transparent 75%),
      linear-gradient(160deg, var(--photo-dark) 0%, var(--photo-mid) 50%, var(--photo-dark) 100%);
    border-right: 2px solid var(--divider);
  }
  .card__brand {
    position: absolute;
    left: 468px;
    right: 0;
    top: 0;
    height: 348px;
    text-align: center;
  }
  .brand-name {
    position: absolute;
    left: 0;
    right: 0;
    top: 180px;
    font-size: 50px;
    font-weight: 600;
    color: var(--mauve);
    letter-spacing: 0.5px;
  }
  .brand-tagline {
    position: absolute;
    left: 0;
    right: 0;
    top: 285px;
    font-size: 36px;
    font-weight: 700;
    color: var(--mauve);
    letter-spacing: -1px;
  }
  .card__contact {
    position: absolute;
    left: 468px;
    right: 0;
    top: 348px;
    bottom: 0;
    background: var(--mauve);
    border-top: 4px solid var(--mauve-deep);
    color: var(--white);
    padding-left: 57px;
  }
  .contact-name {
    position: absolute;
    top: 18px;
    font-size: 52px;
    font-weight: 700;
    letter-spacing: -0.5px;
    line-height: 1;
  }
  .contact-role {
    position: absolute;
    top: 78px;
    font-size: 30px;
    font-weight: 700;
    line-height: 1;
  }
  .contact-list {
    position: absolute;
    top: 150px;
    list-style: none;
    font-size: 38px;
    font-weight: 700;
    letter-spacing: -0.5px;
    line-height: 58px;
  }
</style>
</head>
<body>
  <main class="card">
    <div class="card__photo" role="img" aria-label="Black and white photograph of a couple's clasped hands, one wearing an engagement ring"></div>

    <section class="card__brand">
      <p class="brand-name">The Tidewell Bureau</p>
      <p class="brand-tagline">Helping You Find The "One"</p>
    </section>

    <section class="card__contact">
      <h1 class="contact-name">Mavis Ellery</h1>
      <p class="contact-role">Matchmaker</p>
      <ul class="contact-list">
        <li>Tel. 0492 517 264</li>
        <li>mavis@tidewellbureau.com.au</li>
        <li>www.tidewellbureau.com.au</li>
      </ul>
    </section>
  </main>
</body>
</html>
```